Harrow Grading LLC business card design

Excavation company business cards

Contact Information for Business Card

Harrow Grading LLC cell phone 208-417-6290 office phone 208-319-4856 harrowgradingllc@maplecove.com Driveways, site prep, retaining walls, septic systems, rock delivery

Colors

Designer to choose colors to be used in the design.

```html
<!DOCTYPE html>
<html lang="en">
<head>
<meta charset="utf-8">
<title>Harrow Grading LLC – Business Card</title>
<link href="https://fonts.googleapis.com/css2?family=Montserrat:wght@400;500;800&family=Archivo+Narrow:wght@500&display=swap" rel="stylesheet">
<style>
  :root{
    --orange:#e8620f;
    --orange-deep:#e05a0a;
    --white:#ffffff;
    --peach:#f6d3c2;
    --ink:#3a3a3a;
    --backdrop:#d9d9d9;
  }
  *{box-sizing:border-box;margin:0;padding:0}
  html,body{width:1200px;height:800px;overflow:hidden}
  body{
    background:var(--backdrop);
    font-family:'Montserrat',Arial,sans-serif;
    display:flex;flex-direction:column;align-items:center;justify-content:center;gap:36px;
  }
  .card{
    position:relative;width:620px;height:354px;border-radius:22px;overflow:hidden;
    background:var(--orange);
  }
  /* front */
  .card-front .art-field{position:absolute;inset:0}
  .contact-block{position:absolute;left:46px;top:186px;color:var(--white)}
  .contact-name{font-weight:800;font-size:21px;letter-spacing:1.5px;text-transform:uppercase;line-height:1}
  .contact-role{font-weight:400;font-size:13px;letter-spacing:.5px;margin-top:6px;opacity:.95}
  .contact-list{list-style:none;margin-top:14px}
  .contact-list li{display:flex;align-items:center;gap:9px;font-size:13px;font-weight:500;line-height:1.6}
  .contact-list svg{width:13px;height:13px;flex:none}
  .edge-tab{position:absolute;left:0;top:250px;width:14px;height:38px;background:var(--white)}
  .front-brand{
    position:absolute;left:380px;top:146px;width:220px;
    text-align:center;color:var(--orange);font-weight:800;font-size:28px;line-height:1.1;
    text-transform:uppercase;letter-spacing:1px;
  }
  .front-brand .brand-dot{display:inline-block;width:11px;height:11px;border-radius:50%;background:var(--orange);margin-right:8px;vertical-align:middle}
  .service-line{
    position:absolute;left:372px;top:262px;width:236px;text-align:center;
    font-family:'Archivo Narrow',Arial,sans-serif;font-weight:500;font-size:14px;line-height:1.45;color:var(--ink);
  }
  .service-line .sep{color:var(--orange);margin:0 4px}
  /* back */
  .card-back{background:var(--orange-deep);display:flex;align-items:center;justify-content:center;padding:0 60px}
  .back-brand{color:var(--white);font-weight:800;font-size:34px;letter-spacing:1.5px;text-transform:uppercase;text-align:center;line-height:1.1}
</style>
</head>
<body>

  <section class="card card-front" aria-label="Business card front">
    <svg class="art-field" viewBox="0 0 620 354" aria-hidden="true">
      <polygon points="334,354 366,240 356,150 398,70 432,30 486,0 620,0 620,354" fill="#ffffff"/>
    </svg>
    <svg class="art-field" viewBox="0 0 620 354" role="img" aria-label="Illustration of mountains with an excavator">
      <defs>
        <linearGradient id="artTone" x1="0" y1="0" x2="1" y2="1">
          <stop offset="0" stop-color="#f6d3c2"/>
          <stop offset="1" stop-color="#ffffff"/>
        </linearGradient>
      </defs>
      <polygon points="370,250 374,160 404,90 450,45 514,15 620,10 620,250" fill="url(#artTone)" opacity=".85"/>
    </svg>

    <div class="front-brand"><span class="brand-dot"></span>Harrow Grading LLC</div>
    <p class="service-line">Driveways<span class="sep">•</span>Site Prep<span class="sep">•</span>Retaining Walls<br>Septic Systems<span class="sep">•</span>Rock Delivery</p>

    <div class="edge-tab"></div>
    <div class="contact-block">
      <h1 class="contact-name">Travis Holloway</h1>
      <p class="contact-role">President</p>
      <ul class="contact-list">
        <li>
          <svg viewBox="0 0 16 16" aria-label="Office phone"><path d="M3 1l3 3-1.5 2a9 9 0 0 0 5.5 5.5L12 10l3 3-2 2C7 15 1 9 1 3z" fill="#fff"/></svg>
          208-319-4856
        </li>
        <li>
          <svg viewBox="0 0 16 16" aria-label="Cell phone"><rect x="4" y="1" width="8" height="14" rx="1.5" fill="none" stroke="#fff" stroke-width="1.6"/></svg>
          208-417-6290
        </li>
        <li>
          <svg viewBox="0 0 16 16" aria-label="Email"><rect x="1" y="3" width="14" height="10" fill="#fff"/><path d="M1 3l7 6 7-6" fill="none" stroke="#e8620f" stroke-width="1.4"/></svg>
          harrowgradingllc@maplecove.com
        </li>
      </ul>
    </div>
  </section>

  <section class="card card-back" aria-label="Business card back">
    <p class="back-brand">Harrow Grading LLC</p>
  </section>

</body>
</html>
```